Digital course framework design and style

We need a design for a framework to be used on an online course. The framework will have several layers and needs to have a style which can be followed throughout the course. The attached image is at the top level.

Need to keep to the triangle shape and the colour green and red for the words shown in the illustration. The three inner sections are pillars/pathways which we will expand out (Health, Adventure, Creativity) .
The course is Clouded Skies Clearing (the inner section) so we need to show the flow from being frustrated with your kids on devices and not trying to be a successful and they can be, moving them to there kids taking action and frustration reducing. So important the framework has the feeling of progression and movement. The issue for each pillar/paths is the red text and the green being the result.

I want the framework to be simple to understand keeping to line diagram but introducing an icon for each piller/path. Needs to look professional and engaging.

I need to be able to edit the framework, present it elements so be in a format I can hide each Piller and display on a mouse click so layered.

Colours should fit into the brand colours

Core colour: #f07f37
Black secondary: #070707
Green : #0A633B
White: #FFFEFE

Website for brand approach: www.bramblewoodhollow.com

Target Market(s)

Parents of children spending too long on devices

Font styles to use
Sans Serif

Requirements
Must have
• Clear and easy to see outcomes (green words on the example)
Flow from problem to solution (Clouded Skies Clearing)
Style to be extended to further piller designs including icons for Health, Adventure, Creativity
Ability to present 1) the promise Clouded Skies Clearing 2) each piller in turn
Brand colours included in brief
Should not have
• Busy complicated slide
Keep to line art not complex images

```html
<!DOCTYPE html>
<html lang="en">
<head>
<meta charset="utf-8">
<title>The Ignite Pathway</title>
<link rel="stylesheet" href="https://fonts.googleapis.com/css2?family=Roboto+Condensed:wght@400;500;700&display=swap">
<style>
  :root {
    --orange: #f07f37;
    --black: #070707;
    --green: #0a633b;
    --red: #e3262b;
    --white: #fffefe;
  }
  * { margin: 0; padding: 0; box-sizing: border-box; }
  html, body { width: 1200px; height: 1000px; overflow: hidden; background: var(--white); }
  .canvas {
    position: relative;
    width: 1200px;
    height: 1000px;
    font-family: "Roboto Condensed", "Arial Narrow", sans-serif;
    background: var(--white);
  }
  .title-block {
    position: absolute;
    left: 311px;
    top: 44px;
    width: 578px;
  }
  .title-block__heading {
    background: var(--black);
    color: var(--orange);
    height: 58px;
    font-size: 42px;
    font-weight: 700;
    letter-spacing: 1px;
    text-align: center;
    line-height: 58px;
  }
  .title-block__sub {
    border: 3px solid var(--black);
    border-top: none;
    height: 50px;
    color: var(--orange);
    font-size: 25px;
    font-weight: 500;
    text-align: center;
    line-height: 46px;
  }
  .diagram { position: absolute; left: 0; top: 0; }
  .ring-arc { fill: none; stroke: var(--orange); stroke-width: 7; }
  .outcome { fill: var(--green); font-size: 31px; font-weight: 500; }
  .issue { fill: var(--red); font-size: 18px; font-weight: 500; }
  .pillar-name { fill: var(--orange); font-size: 27px; font-weight: 700; }
  .core-triangle { fill: none; stroke: var(--black); stroke-width: 13; stroke-linejoin: miter; }
  .badge { fill: var(--black); }
  .badge-icon { fill: none; stroke: var(--orange); stroke-width: 3; stroke-linecap: round; stroke-linejoin: round; }
  .badge-fill { fill: var(--orange); }
  .flow-action { fill: var(--green); }
  .flow-action__title { font-size: 20px; font-weight: 700; }
  .flow-action__note { font-size: 16px; }
  .flow-frustration { fill: var(--red); }
  .flow-frustration__title { font-size: 20px; font-weight: 700; }
  .flow-frustration__note { font-size: 16px; }
  .flow-arrow { stroke: var(--green); stroke-width: 6; }
  .brand-mark {
    position: absolute;
    left: 860px;
    top: 876px;
    display: flex;
    align-items: center;
    gap: 8px;
    color: var(--black);
    font-size: 20px;
    font-weight: 500;
    line-height: 1.05;
  }
  .brand-mark__square { width: 14px; height: 14px; background: var(--black); flex: none; }
</style>
</head>
<body>
<main class="canvas">
  <header class="title-block">
    <h1 class="title-block__heading">THE IGNITE PATHWAY</h1>
    <p class="title-block__sub">The 3 Paths To Grow Positivity In Your Kids</p>
  </header>

  <svg class="diagram" width="1200" height="1000" viewBox="0 0 1200 1000" xmlns="http://www.w3.org/2000/svg">
    <defs>
      <path id="outcome-path-health" d="M292.6 712.5 A355 355 0 0 1 450 213.3"/>
      <path id="outcome-path-creativity" d="M750 213.3 A355 355 0 0 1 907.4 712.5"/>
      <path id="outcome-path-adventure" d="M310.5 778 A378 378 0 0 0 889.5 778"/>
      <marker id="arrow-head" viewBox="0 0 10 10" refX="5" refY="5" markerWidth="3.6" markerHeight="3.6" orient="auto">
        <path d="M0 0 L10 5 L0 10 z" fill="#0a633b"/>
      </marker>
    </defs>

    <!-- outcome ring -->
    <g class="ring">
      <path class="ring-arc" d="M414.8 249.8 A340 340 0 0 1 770 240.6"/>
      <path class="ring-arc" d="M297.1 689.4 A340 340 0 0 0 341.5 755.8"/>
      <path class="ring-arc" d="M858.5 755.8 A340 340 0 0 0 902.9 689.4"/>
    </g>

    <g class="outcomes">
      <text class="outcome"><textPath href="#outcome-path-health" startOffset="50%" text-anchor="middle">Balanced, Fit, Energetic &amp; Focused</textPath></text>
      <text class="outcome"><textPath href="#outcome-path-creativity" startOffset="50%" text-anchor="middle">Bright, Ideas driven, Positive &amp; Motivated</textPath></text>
      <text class="outcome"><textPath href="#outcome-path-adventure" startOffset="50%" text-anchor="middle">Curious, Connected, Excited &amp; Leading</textPath></text>
    </g>

    <!-- issues -->
    <g class="issues">
      <text class="issue" transform="translate(428 462) rotate(-65)" text-anchor="middle">ANXIOUS, OVERWEIGHT, UNFIT &amp; DISCONNECTED</text>
      <text class="issue" transform="translate(763 468) rotate(65)" text-anchor="middle">UNIMAGINATIVE, NEGATIVE, SCREEN - FOCUSED &amp; TRAPPED</text>
      <text class="issue" x="607" y="806" text-anchor="middle">INACTIVE, INSULAR, SOLITARY &amp; TIMID</text>
    </g>

    <!-- core triangle -->
    <polygon class="core-triangle" points="598,232 364,741 836,741"/>

    <!-- pillar names -->
    <g class="pillars">
      <text class="pillar-name" transform="translate(516 536) rotate(-65)" text-anchor="middle">HEALTH</text>
      <text class="pillar-name" transform="translate(672 540) rotate(65)" text-anchor="middle">CREATIVITY</text>
      <text class="pillar-name" x="600" y="702" text-anchor="middle">ADVENTURE</text>
    </g>

    <!-- flow -->
    <g class="flow">
      <text class="flow-action" text-anchor="middle">
        <tspan class="flow-action__title" x="599" y="374">Action</tspan>
        <tspan class="flow-action__note" x="599" y="398">(in your kids)</tspan>
      </text>
      <line class="flow-arrow" x1="598" y1="585" x2="598" y2="424" marker-end="url(#arrow-head)"/>
      <text class="flow-frustration" text-anchor="middle">
        <tspan class="flow-frustration__note" x="600" y="611">(your)</tspan>
        <tspan class="flow-frustration__title" x="597" y="636">Frustation</tspan>
      </text>
    </g>

    <!-- pillar badges -->
    <g class="badge-health">
      <circle class="badge" cx="468" cy="515" r="28"/>
      <path class="badge-fill" d="M468 533 C455 523 450 515 450 508 C450 501 455 497 460 497 C464 497 467 500 468 503 C469 500 472 497 476 497 C481 497 486 501 486 508 C486 515 481 523 468 533 Z"/>
      <path d="M452 513 L460 513 L463 506 L467 522 L471 509 L474 513 L484 513" fill="none" stroke="#070707" stroke-width="2.2" stroke-linejoin="round"/>
    </g>
    <g class="badge-creativity">
      <circle class="badge" cx="728" cy="516" r="28"/>
      <circle class="badge-icon" cx="728" cy="516" r="9"/>
      <circle class="badge-fill" cx="728" cy="516" r="3.5"/>
      <path class="badge-icon" d="M728 500 V504 M728 528 V532 M712 516 H716 M740 516 H744 M717 505 L720 508 M736 524 L739 527 M739 505 L736 508 M720 524 L717 527"/>
    </g>
    <g class="badge-adventure">
      <circle class="badge" cx="598" cy="746" r="28"/>
      <rect class="badge-fill" x="588" y="730" width="20" height="32" rx="6" role="img" aria-label="Hiker icon"/>
    </g>
  </svg>

  <div class="brand-mark">
    <span class="brand-mark__square"></span>
    <span class="brand-mark__name">Bramblewood<br>Hollow</span>
  </div>
</main>
</body>
</html>
```